Design NEW business card

We would like a business card using the colour deep red wine or dark navy blue textured background (patterned or not, open to suggestions) with a high gloss debossed rose gold/copper RM Roland Mercer Jewellery business name (Provided). I have included images for your review we would like to keep our currently logo and business name on the front but you can change the layout and positioning. For the back of the card we are open to all suggestions/variations.
Business
Use our current RM Roland Mercer Jewellery logo (Provided image)

```html
<!DOCTYPE html>
<html lang="en">
<head>
<meta charset="utf-8">
<title>Roland Mercer Jewellery – Business Card</title>
<link rel="stylesheet" href="https://fonts.googleapis.com/css2?family=Montserrat:wght@300;400&family=Roboto:wght@400&display=swap">
<style>
  :root {
    --backdrop: #c9c9c9;
    --paper: #f7f7f6;
    --wine: #5a2229;
    --copper: #b8856a;
    --copper-light: #deab88;
    --copper-dark: #98694a;
    --silver: #c4c4c4;
    --ink-grey: #555555;
    --white: #ffffff;
  }
  * { margin: 0; padding: 0; box-sizing: border-box; }
  html, body { width: 1200px; height: 960px; overflow: hidden; }
  body {
    background: var(--backdrop);
    font-family: "Montserrat", Arial, sans-serif;
    position: relative;
  }
  .card {
    position: absolute;
    width: 600px;
    height: 342px;
    left: 320px;
    box-shadow: 0 2px 6px rgba(0,0,0,.25);
    overflow: hidden;
  }
  /* Front */
  .card-front { top: 96px; background: var(--paper); }
  .brand {
    position: absolute;
    color: var(--copper);
    font-weight: 300;
    text-align: center;
    text-transform: uppercase;
    line-height: 1;
  }
  .card-front .brand { left: 0; width: 600px; top: 108px; }
  .brand-initials { font-size: 64px; letter-spacing: 4px; }
  .brand-name { font-size: 23px; letter-spacing: 4px; margin-top: 14px; }
  .brand-sub { font-size: 10px; letter-spacing: 12px; margin-top: 9px; }
  .website-front {
    position: absolute;
    left: 0; width: 600px; top: 306px;
    text-align: center;
    font-family: "Roboto", Arial, sans-serif;
    font-size: 15px;
    letter-spacing: 5px;
    color: var(--ink-grey);
  }
  /* Back */
  .card-back { top: 493px; background: var(--wine); }
  .back-shapes { position: absolute; inset: 0; }
  .card-back .brand { left: 38px; width: 250px; top: 34px; }
  .card-back .brand-initials { font-size: 58px; }
  .card-back .brand-name { font-size: 19px; letter-spacing: 3px; margin-top: 16px; }
  .card-back .brand-sub { font-size: 8px; letter-spacing: 11px; margin-top: 8px; }
  .person {
    position: absolute;
    right: 36px; top: 38px;
    text-align: right;
    color: var(--white);
  }
  .person-name { font-size: 20px; font-weight: 400; letter-spacing: .3px; }
  .person-title { font-size: 13px; margin-top: 6px; }
  .address {
    position: absolute;
    right: 38px; top: 164px;
    text-align: right;
    color: var(--white);
    font-size: 14px;
    line-height: 20px;
  }
  .contacts {
    position: absolute;
    right: 38px; top: 212px;
    list-style: none;
    color: var(--white);
    font-size: 14px;
    line-height: 19px;
    text-align: right;
  }
  .contacts li { display: flex; justify-content: flex-end; align-items: center; gap: 7px; }
  .contacts svg { width: 13px; height: 13px; flex: none; }
</style>
</head>
<body>

<section class="card card-front" aria-label="Card front">
  <div class="brand">
    <div class="brand-initials">RM</div>
    <div class="brand-name">Roland Mercer</div>
    <div class="brand-sub">Jewellery</div>
  </div>
  <div class="website-front">www.rolandmercer.com</div>
</section>

<section class="card card-back" aria-label="Card back">
  <svg class="back-shapes" width="600" height="342" viewBox="0 0 600 342">
    <defs>
      <radialGradient id="copperGlow" cx="0.55" cy="0.4" r="0.6">
        <stop offset="0" stop-color="var(--copper-light)"/>
        <stop offset="1" stop-color="var(--copper-dark)"/>
      </radialGradient>
    </defs>
    <path class="silver-stripe" d="M388 0 Q284 120 258 342 L278 342 Q304 120 398 0 Z" fill="var(--silver)"/>
    <path class="copper-panel" d="M400 0 Q306 120 280 342 L600 342 L600 0 Z" fill="url(#copperGlow)"/>
  </svg>

  <div class="brand">
    <div class="brand-initials">RM</div>
    <div class="brand-name">Roland Mercer</div>
    <div class="brand-sub">Jewellery</div>
  </div>

  <div class="person">
    <div class="person-name">DANIEL AVERY</div>
    <div class="person-title">CEO/FOUNDER</div>
  </div>

  <address class="address" style="font-style:normal">
    2140 Willow Crest Road<br>Harbor Bend, Alaska 34512
  </address>

  <ul class="contacts">
    <li>555 214 7380
      <svg viewBox="0 0 16 16" aria-hidden="true"><path fill="#fff" d="M3 1l3 3-1.5 2a9 9 0 0 0 5.5 5.5L12 10l3 3-2 2C7 15 1 9 1 3z"/></svg></li>
    <li>555 362 9104
      <svg viewBox="0 0 16 16" aria-hidden="true"><rect x="4" y="1" width="8" height="14" rx="1.5" fill="none" stroke="#fff" stroke-width="1.6"/><circle cx="8" cy="12.5" r="0.9" fill="#fff"/></svg></li>
    <li>555 718 2265
      <svg viewBox="0 0 16 16" aria-hidden="true"><rect x="4" y="1" width="8" height="5" fill="#fff"/><rect x="1" y="6" width="14" height="7" rx="1" fill="#fff"/><rect x="4" y="10" width="8" height="5" fill="#fff" stroke="var(--copper-dark)" stroke-width="1"/></svg></li>
    <li>hello@rolandmercer.com
      <svg viewBox="0 0 16 16" aria-hidden="true"><rect x="1" y="3" width="14" height="10" fill="#fff"/><path d="M1 3l7 6 7-6" fill="none" stroke="var(--copper-dark)" stroke-width="1.2"/></svg></li>
    <li>www.rolandmercer.com
      <svg viewBox="0 0 16 16" aria-hidden="true"><circle cx="8" cy="8" r="6.5" fill="#fff"/><path d="M5 4c2 1 1 3 3 3s1 3 3 4M9 2c-1 2 1 2 2 3" fill="none" stroke="var(--copper-dark)" stroke-width="1.2"/></svg></li>
  </ul>
</section>

</body>
</html>
```